pathology learning flashcard template graphic design .

Creative designs for 2 sides of the flashcards to include colorful sectioning and font sizes that will make it easy to use in studying.

```html
<!DOCTYPE html>
<html lang="en">
<head>
<meta charset="utf-8">
<title>Achalasia – Pathology Flashcard</title>
<link rel="stylesheet" href="https://fonts.googleapis.com/css2?family=Arvo:wght@400;700&family=Roboto:ital,wght@0,400;1,400&display=swap">
<style>
  :root {
    --navy: #2f4486;
    --heading-navy: #25336a;
    --alert-red: #e0322c;
    --ink: #2b2b2b;
    --front-bg-a: #eef2f8;
    --front-bg-b: #dfe7f1;
    --rx-bg-a: #e3f4f7;
    --rx-bg-b: #d2edf2;
    --teal-rule: #33c1d1;
    --case-bg-a: #cdebee;
    --case-bg-b: #bfe5ea;
    --case-green: #1d8a4d;
    --sources-bg-a: #cfe9f7;
    --sources-bg-b: #5fb0e6;
    --sources-ink: #2e3f63;
    --white: #ffffff;
  }
  * { box-sizing: border-box; margin: 0; padding: 0; }
  html, body { width: 1200px; height: 824px; overflow: hidden; background: var(--white); }
  body { font-family: "Roboto", Arial, sans-serif; color: var(--ink); }

  .card { position: relative; width: 1200px; height: 824px; display: flex; }

  /* Front side */
  .card-front {
    position: relative; width: 600px; height: 824px;
    background: linear-gradient(160deg, var(--front-bg-a) 0%, var(--front-bg-b) 100%);
  }
  .card-title {
    height: 95px; background: var(--navy); color: var(--white);
    font-family: "Arvo", Georgia, serif; font-weight: 400;
    font-size: 42px; letter-spacing: 2.5px;
    padding: 26px 0 0 42px;
  }
  .section { position: absolute; left: 45px; width: 507px; }
  .section-heading {
    font-family: "Arvo", Georgia, serif; font-weight: 400;
    font-size: 24px; color: var(--heading-navy); letter-spacing: 0.5px;
    margin-bottom: 10px;
  }
  .section-heading.is-alert { color: var(--alert-red); }
  .section-text {
    font-size: 17.5px; line-height: 26.5px; text-align: justify;
  }
  .section-definition { top: 126px; }
  .section-etiology { top: 250px; }
  .section-symptoms { top: 408px; }
  .section-diagnosis { top: 567px; left: 48px; }

  /* Back side */
  .card-back { position: relative; width: 600px; height: 824px; }
  .treatment {
    position: absolute; top: 0; left: 0; width: 600px; height: 232px;
    background: linear-gradient(160deg, var(--rx-bg-a), var(--rx-bg-b));
    padding: 46px 45px 0 46px;
  }
  .treatment .section-heading { margin-bottom: 8px; }
  .rule { position: absolute; top: 232px; left: 0; width: 600px; height: 8px; background: var(--teal-rule); }
  .case {
    position: absolute; top: 240px; left: 0; width: 600px; height: 414px;
    background: linear-gradient(170deg, var(--case-bg-a), var(--case-bg-b));
    padding: 26px 45px 0 46px;
  }
  .case-heading {
    font-family: "Arvo", Georgia, serif; font-weight: 400;
    font-size: 29px; color: var(--case-green); margin-bottom: 12px;
  }
  .case .section-text { line-height: 27px; }
  .sources {
    position: absolute; top: 654px; left: 0; width: 600px; height: 170px;
    background: linear-gradient(115deg, var(--sources-bg-a) 0%, var(--sources-bg-a) 55%, var(--sources-bg-b) 100%);
    padding: 24px 45px 0 46px;
    font-style: italic; color: var(--sources-ink); font-size: 18px; line-height: 27px;
  }
</style>
</head>
<body>
<main class="card">
  <section class="card-front" role="img" aria-label="Front of flashcard over a soft pale-blue background of faint anatomical imagery">
    <h1 class="card-title">ACHALASIA</h1>

    <div class="section section-definition">
      <h2 class="section-heading">Definition:</h2>
      <p class="section-text">Motility disorder where esophageal relaxation is impaired in the lower esophageal sphincter (LES).</p>
    </div>

    <div class="section section-etiology">
      <h2 class="section-heading">Etiology/Pathology:</h2>
      <p class="section-text">Destruction of inhibitory neurons in the Auerbach plexus.&nbsp; Loss of peristalsis in the lower esophageal sphincter (Lower-two thirds of the esophagus).</p>
    </div>

    <div class="section section-symptoms">
      <h2 class="section-heading is-alert">P/E and Symptoms:</h2>
      <p class="section-text">Dysphagia that is progressive, regurgitation, weight-loss, dry cough, chest pain, GERD, esophageal perforation, squamous cell carcinoma, aspiration pneumonia.</p>
    </div>

    <div class="section section-diagnosis">
      <h2 class="section-heading">Dx:</h2>
      <p class="section-text">Barium swallow will show ‘bird’s beak’ and esophageal dilation.&nbsp; Manometry will present with increased resting lower esophageal sphincter pressure. Endoscopy will usually present with normal mucosa and LES dilation, and in some cases residual material such as undigested food particles may be present.</p>
    </div>
  </section>

  <section class="card-back">
    <div class="treatment">
      <h2 class="section-heading">Rx:</h2>
      <p class="section-text">First line of treatment are nitrates, calcium channel blockers, and Botulinum toxin injection in the LES. Long term management options include esophageal dilation with pneumatic balloon and myotomy.</p>
    </div>
    <div class="rule"></div>
    <div class="case">
      <h2 class="case-heading">C- Achalasia</h2>
      <p class="section-text">Symptoms and studies suggestive of achalasia. Patient’s manometry presents with no relaxation of the lower esophageal sphincter during swallowing. Patient also complains of dysphagia and is unable to swallow properly, leading to weight loss.&nbsp; Patient has no past infection or inflammation, ruling out eosinophilic esophagitis.&nbsp; Patient does not have chronic GERD, eliminating the possibility of Barrett esophagus, in which at least 5 years of acid reflux are beforehand to develop columnar metaplasia.</p>
    </div>
    <div class="sources">
      <p>Sources:</p>
      <p>Clinical Drug Handbook; Pocket Pharmacology Guide; RxReference.com; MedNotesOnline.com</p>
    </div>
  </section>
</main>
</body>
</html>
```